Safety Company in need of a Tri-fold Brochure design

We need a tri-fold brochure for our technicians to hand out to clients. We need to show the services we provide. Design, engineering, fabrication, installation, testing, Operating/Work procedures, training, certification of Fall Protection/Window Cleaning Equipment.

Target Market(s)

building owners, property managers

Industry/Entity Type

It Company

Font styles to use
Sans Serif
Script

Colors
0455a3
ec1f27
ffffff

Requirements
Must have
• mission statement, 24 hour response policy, photos of services

```html
<!DOCTYPE html>
<html lang="en">
<head>
<meta charset="utf-8">
<title>Harlow Safety – Tri-fold Brochure</title>
<link href="https://fonts.googleapis.com/css2?family=Oswald:wght@500;700&family=Arimo:wght@400;700&display=swap" rel="stylesheet">
<style>
:root{
  --blue:#0455a3;
  --blue-box:#3274b8;
  --red:#ec1f27;
  --white:#ffffff;
  --ink:#111111;
  --panel-grey:#e9ebee;
  --frame:#5a6472;
}
*{margin:0;padding:0;box-sizing:border-box}
html,body{width:1200px;height:853px;overflow:hidden;background:var(--white)}
.brochure{position:relative;width:1200px;height:853px;font-family:'Arimo',sans-serif;color:var(--ink)}
.panel{position:absolute;top:0;height:853px;width:400px;overflow:hidden}
.panel--left{left:0;background:linear-gradient(90deg,#e4e6ea,#f7f8f9 60%,#eceef1)}
.panel--middle{left:400px;background:var(--white)}
.panel--right{left:800px}

.section-tab{position:absolute;left:0;top:18px;width:375px;height:41px;background:var(--blue);border-radius:0 22px 22px 0;color:var(--white);font-family:'Oswald',sans-serif;font-weight:500;font-size:20px;line-height:41px;padding-left:18px;letter-spacing:.3px;word-spacing:5px}
.intro{position:absolute;left:15px;top:64px;width:380px;font-size:12.6px;font-weight:700;line-height:17.8px;color:#1a1a1a}
.intro p+p{margin-top:18px}
.works-title{position:absolute;left:0;width:387px;top:297px;text-align:center;font-family:'Oswald',sans-serif;font-weight:700;font-size:19px}
.works-grid{position:absolute;left:35px;top:332px;width:322px}
.work{position:absolute;width:151px;height:115px;border-radius:14px;background:linear-gradient(#f4f5f7,#c9ccd1);border:2px solid #9aa0a8;padding:10px}
.work .photo{width:100%;height:100%;border-radius:8px;border:3px solid var(--frame)}
.work-dot{position:absolute;width:36px;height:36px;border-radius:50%;background:radial-gradient(circle at 40% 35%,#ff8a8a,var(--red) 60%,#b1141a);border:3px solid #d9dbe0;box-shadow:0 0 0 2px #6b7380}

.mission{position:absolute;left:8px;top:32px;width:384px;text-align:center;font-family:'Oswald',sans-serif;font-weight:700;font-size:21.5px;line-height:27px;text-transform:uppercase;letter-spacing:-.2px}
.contact-card{position:absolute;left:25px;top:383px;width:352px;height:283px;background:var(--blue-box);border-radius:16px;color:var(--white)}
.toll-label{position:absolute;left:0;width:100%;top:14px;text-align:center;font-family:'Oswald',sans-serif;font-weight:700;font-size:27px;padding-left:8px}
.toll-number{position:absolute;left:84px;top:42px;font-size:34px;font-weight:700}
.icon{position:absolute}
.addr{position:absolute;font-size:13.5px;font-weight:700;line-height:20.5px}
.addr--street{left:40px;top:112px}
.addr--box{left:232px;top:110px}
.divider{position:absolute;left:177px;top:120px;width:2px;height:60px;background:var(--white)}
.contact-line{position:absolute;font-size:14.5px;font-weight:700}
.partners-title{position:absolute;left:0;width:100%;top:702px;text-align:center;font-size:14.5px;font-weight:700;padding-left:14px}
.badge{position:absolute;background:#d6d9de}

.city-photo{position:absolute;inset:0;background:linear-gradient(160deg,#dfe4ea 0%,#b9c2cc 30%,#7f8a96 60%,#5a636d 100%)}
.swoosh{position:absolute;left:0;top:0}
.brand{position:absolute;left:28px;top:62px;display:flex;align-items:center;gap:10px;font-family:'Oswald',sans-serif;font-weight:700;font-size:26px;color:var(--blue)}
.brand-mark{width:18px;height:18px;border-radius:50%;background:var(--blue)}
.tagline{position:absolute;left:255px;top:18px;font-family:'Oswald',sans-serif;font-weight:700;font-size:31px;line-height:35.5px;color:var(--red)}
.response-badge{position:absolute;left:826px;top:210px}
.response-text{position:absolute;left:842px;top:258px;width:148px;text-align:center;font-family:'Oswald',sans-serif;font-weight:700;color:var(--red);line-height:.95}
.response-text .big{font-size:40px;display:block}
.response-text .small{font-size:30px;display:block}
.ribbon{position:absolute;left:800px;top:735px}
.ribbon-text{position:absolute;left:804px;top:760px;font-family:'Oswald',sans-serif;font-weight:700;font-size:21px;color:var(--white);transform:rotate(-1deg)}
</style>
</head>
<body>
<main class="brochure">

  <section class="panel panel--left">
    <h2 class="section-tab">OPOS Documentation / Work Plan</h2>
    <div class="intro">
      <p>An OPOS, or Operating Procedure Outline Sheet, verifies the equipment on the building to be used for window cleaning and exterior building maintenance procedures. Per California code, it must include a number of elements in pictorial and written form to instruct employees about safe use of roof supported building maintenance equipment and/or procedures for window cleaning.</p>
      <p>We are the industry-leader in providing OPOS documents and we develop the building specific document, as required by CA OSHA, as well as the Work Plan, a Fed OSHA required document, for exterior building maintenance equipment.</p>
    </div>
    <h3 class="works-title">SOME OF OUR WORKS</h3>
    <div class="works-grid">
      <div class="work" style="left:0;top:0"><div class="photo" role="img" aria-label="Rooftop davit arm and suspended platform" style="background:linear-gradient(#9fb8d6,#e7ecf1 60%,#b3b6ba)"></div></div>
      <div class="work" style="left:171px;top:0"><div class="photo" role="img" aria-label="Roof plan drawing of equipment layout" style="background:linear-gradient(#f2f4f7,#d9e0ea)"></div></div>
      <div class="work" style="left:0;top:122px"><div class="photo" role="img" aria-label="Technicians testing anchors beside a building" style="background:linear-gradient(#8aa070,#c9c0b0 50%,#6e7d52)"></div></div>
      <div class="work" style="left:171px;top:122px"><div class="photo" role="img" aria-label="Safety training class in a meeting room" style="background:linear-gradient(#c9c2b4,#8e7f6c)"></div></div>
      <div class="work" style="left:0;top:244px"><div class="photo" role="img" aria-label="Building facade with guardrail ledge" style="background:linear-gradient(#7c838c,#c3c6c9 60%,#9ea2a6)"></div></div>
      <div class="work" style="left:171px;top:244px"><div class="photo" role="img" aria-label="Rooftop guardrail installation" style="background:linear-gradient(#aab8c4,#6d7782)"></div></div>
      <div class="work" style="left:0;top:366px"><div class="photo" role="img" aria-label="Roof anchor hardware on tiled roof" style="background:linear-gradient(#8a5a44,#b68a70)"></div></div>
      <div class="work" style="left:171px;top:366px"><div class="photo" role="img" aria-label="Crew working on a suspended platform" style="background:linear-gradient(#a9c0d8,#d8dde3 55%,#5c6470)"></div></div>
      <span class="work-dot" style="left:142px;top:85px"></span>
      <span class="work-dot" style="left:142px;top:207px"></span>
      <span class="work-dot" style="left:142px;top:329px"></span>
      <span class="work-dot" style="left:142px;top:451px"></span>
    </div>
  </section>

  <section class="panel panel--middle">
    <p class="mission">For over 42 years we have been doing our most important duty, providing buildings with a safe working environment. We are proficient in finding solutions of value and provide you and your workers a safe work environment. Our service and equipment is always state of the art and in line with all regulations and certification approval standards</p>

    <div class="contact-card">
      <div class="toll-label">TOLL FREE</div>
      <svg class="icon" style="left:20px;top:45px" width="34" height="42" viewBox="0 0 34 42"><path d="M6 2l8 0 3 10-5 4c2 6 6 12 11 15l4-4 8 5-2 8c-14 0-28-18-27-38z" fill="var(--white)"/></svg>
      <div class="toll-number">(800) 555-0142</div>
      <svg class="icon" style="left:14px;top:109px" width="20" height="28" viewBox="0 0 20 28"><path d="M10 0a10 10 0 0 1 10 10c0 7-10 18-10 18S0 17 0 10A10 10 0 0 1 10 0z" fill="var(--white)"/><circle cx="10" cy="10" r="4" fill="var(--blue-box)"/></svg>
      <div class="addr addr--street">482 Alder Loop<br>Suite A<br>Brentmoor, CA 94000</div>
      <div class="divider"></div>
      <svg class="icon" style="left:202px;top:111px" width="24" height="16" viewBox="0 0 24 16"><rect x="1" y="1" width="22" height="14" fill="none" stroke="var(--white)" stroke-width="2"/><path d="M1 1l11 9 11-9" fill="none" stroke="var(--white)" stroke-width="2"/></svg>
      <div class="addr addr--box">PO Box 51240<br>Oak Vale,<br>CA 94001</div>
      <svg class="icon" style="left:86px;top:195px" width="22" height="14" viewBox="0 0 24 16"><rect x="1" y="1" width="22" height="14" fill="none" stroke="var(--white)" stroke-width="2"/><path d="M1 1l11 9 11-9" fill="none" stroke="var(--white)" stroke-width="2"/></svg>
      <div class="contact-line" style="left:116px;top:192px">info@harlowsafety.com</div>
      <svg class="icon" style="left:96px;top:219px" width="28" height="20" viewBox="0 0 28 20"><path d="M2 4l4-2 3 5-3 2c1 3 3 6 6 7l2-2 4 3-2 3C8 20 2 12 2 4z" fill="var(--white)"/><rect x="14" y="2" width="13" height="9" fill="none" stroke="var(--white)" stroke-width="1.6"/><path d="M14 2l6.5 5L27 2" fill="none" stroke="var(--white)" stroke-width="1.6"/></svg>
      <div class="contact-line" style="left:133px;top:219px">(925) 555-0187</div>
      <svg class="icon" style="left:70px;top:249px" width="22" height="22" viewBox="0 0 22 22"><circle cx="11" cy="11" r="9.5" fill="none" stroke="var(--white)" stroke-width="2"/><path d="M4 8h14M4 14h14M11 2c-4 5-4 13 0 18M11 2c4 5 4 13 0 18" fill="none" stroke="var(--white)" stroke-width="1.5"/></svg>
      <div class="contact-line" style="left:105px;top:250px">www.harlowsafety.com</div>
    </div>

    <div class="partners-title">PROUD PARTNERS AND ASSOCIATIONS</div>
    <span class="badge" style="left:35px;top:725px;width:300px;height:32px;border-radius:4px"></span>
    <span class="badge" style="left:30px;top:773px;width:82px;height:44px"></span>
    <span class="badge" style="left:130px;top:770px;width:40px;height:50px"></span>
    <span class="badge" style="left:185px;top:762px;width:46px;height:68px;border-radius:4px"></span>
    <span class="badge" style="left:248px;top:772px;width:92px;height:54px"></span>
  </section>

  <section class="panel panel--right">
    <div class="city-photo" role="img" aria-label="Aerial photo of downtown high-rise towers"></div>
    <svg class="swoosh" width="400" height="853" viewBox="0 0 400 853">
      <path d="M0 315 C120 290 260 235 400 170 L400 215 C270 265 130 315 0 335 Z" fill="var(--blue)"/>
      <path d="M0 0 H400 V170 C260 235 120 290 0 315 Z" fill="var(--white)"/>
    </svg>
    <div class="brand"><span class="brand-mark"></span>Harlow Safety</div>
    <h1 class="tagline">EXTERIOR<br>BUILDING<br>SAFETY<br>SPECIALIST</h1>
  </section>

  <svg class="response-badge" width="180" height="185" viewBox="0 0 180 185">
    <circle cx="90" cy="92" r="88" fill="var(--blue)"/>
    <circle cx="90" cy="92" r="80" fill="var(--red)"/>
    <circle cx="88" cy="90" r="70" fill="#f0f1f3" stroke="#c9ccd1" stroke-width="3"/>
  </svg>
  <div class="response-text"><span class="big">24 HRS</span><span class="small">RESPONSE</span></div>

  <svg class="ribbon" width="285" height="90" viewBox="0 0 285 90">
    <path d="M225 10 L282 18 L262 40 L275 74 L225 64 Z" fill="#03407c"/>
    <path d="M0 10 C90 2 170 0 228 8 L228 60 C170 54 90 56 0 64 Z" fill="var(--blue)" stroke="var(--white)" stroke-width="2"/>
  </svg>
  <div class="ribbon-text">KEEPING TOMORROW SAFER</div>

</main>
</body>
</html>
```